Yoga Magazine needs simple business card!

We are a new yoga magazine and need a simple business card!

I also encourage you to design a text logo and maybe even incorporate some form of the "flower" pattern in the solveralogo.jpg and solverayellow.jpg files attached below. I prefer to have the "solvera" word in larger font and then "San Diego" in smaller font somewhere. See the brickhollow.jpg file or also the tarnwillet.jpg file. Our tag line will be something similar to these. If you could incorporate HEALTH, WELLNESS and YOGA LIFESTYLE into the name somehow that'd be really cool. Maybe even add in FITNESS if there is room. Also, please incorporate MAGAZINE somewhere as I want people to know what we are without having to guess.

we are SOLVERA, San Diego's original magazine for Health, Wellness and the Yoga Lifestyle.

Above all, the business card needs to be classy, clean and sophisticated. I want it to look professional.

I have included a few logos that I like. My favorite colors are the chief.jpg and the kamloops.jpg cards, but that doesn't mean that you have to use orange. I'm just looking for something that stands out.

Target Market(s)

Colors are up to you, but I'm leaning toward something soft and subtle, not bold and obnoxious. Font should be soothing and calm. Include pictures in the brochure of pretty people doing yoga, healthy looking food, families with young children. The target audience is women in their late 20s thru 50s and beyond. We will have some male readers, but maybe on 1/4 of readers will be men...so let's lean toward more feminine than masculine.

Industry/Entity Type

Business

Contact Information for Business Card

Ned Parlow
Editor-In-Chief
Solvera San Diego Magazine
847 Quillon Avenue #310
San Diego, CA 92101
www.brelvaport.com
ned@quorvix.com

Font styles to use
Serif

Requirements
Must have
• mellow, calm colors
• accent mark (') above the "e" in solvera.
Nice to have
• small logos in front of contact information that denote location, globe and phone.
• maybe just flower logo and text name on back? let's be creative here. i'll leave up to you all.
• green? yellow? orange? you pick!
• how about black and green? or green and black? :-)
Should not have
• no pictures or cartoon drawings of people doing yoga poses.
• no photography of people doing yoga poses.

```html
<!DOCTYPE html>
<html lang="en">
<head>
<meta charset="utf-8">
<title>Solvera San Diego – Business Card</title>
<link rel="stylesheet" href="https://fonts.googleapis.com/css2?family=Josefin+Sans:wght@400&family=Open+Sans:wght@400&display=swap">
<style>
  :root {
    --stage-dark: #1c1c1c;
    --stage-mid: #3a3a3a;
    --leaf-green: #8cc63f;
    --leaf-green-deep: #6cbf45;
    --sun-orange: #f7941d;
    --ink: #3b3b3b;
    --card-white: #ffffff;
    --card-mist: #e4e5e7;
  }
  * { box-sizing: border-box; margin: 0; padding: 0; }
  html, body { width: 1200px; height: 999px; overflow: hidden; }
  body { position: relative; font-family: "Open Sans", sans-serif; }

  .stage {
    position: absolute; inset: 0;
    background: radial-gradient(ellipse at 50% 45%, var(--stage-mid) 0%, var(--stage-dark) 75%);
  }

  .brand-lockup {
    position: absolute; left: 0; top: 135px; width: 1200px;
    display: flex; flex-direction: column; align-items: center;
  }
  .brand-dot {
    width: 90px; height: 90px; border-radius: 50%;
    border: 6px solid var(--sun-orange);
    margin-bottom: 82px;
  }
  .brand-name {
    font-family: "Josefin Sans", sans-serif; font-weight: 400;
    font-size: 88px; line-height: 1; letter-spacing: 1px;
    color: var(--leaf-green);
  }
  .brand-place {
    font-family: "Josefin Sans", sans-serif; font-weight: 400;
    font-size: 40px; line-height: 1; letter-spacing: 3px;
    color: var(--sun-orange); margin-top: 12px;
  }

  .card {
    position: absolute; top: 611px; width: 553px; height: 315px;
    border-radius: 28px; overflow: hidden;
  }
  .card--front { left: 18px; background: linear-gradient(to bottom, var(--card-mist) 0%, var(--card-white) 45%); }
  .card--back {
    left: 604px;
    background: linear-gradient(to bottom, var(--leaf-green) 0%, var(--leaf-green-deep) 100%);
    color: var(--card-white); text-align: center;
  }

  .card-brand { position: absolute; left: 24px; top: 18px; display: flex; flex-direction: column; align-items: center; }
  .card-brand .brand-dot { width: 40px; height: 40px; border-width: 3px; margin-bottom: 18px; }
  .card-brand .brand-name { font-size: 33px; letter-spacing: 0; }
  .card-brand .brand-place { font-size: 16px; letter-spacing: 1px; margin-top: 3px; }

  .card-band { position: absolute; left: 0; top: 155px; width: 553px; height: 32px; display: flex; }
  .card-band__solid { width: 277px; background: linear-gradient(to right, #4cb648, var(--leaf-green)); }
  .card-band__fade { flex: 1; background: linear-gradient(to right, #ffffff, var(--leaf-green)); }

  .card-role { position: absolute; left: 24px; top: 191px; font-size: 13px; color: var(--ink); }
  .card-address { position: absolute; left: 24px; top: 226px; font-size: 14px; line-height: 19px; color: var(--ink); font-style: normal; }
  .card-contacts { position: absolute; left: 346px; top: 226px; list-style: none; font-size: 14px; line-height: 19px; color: var(--ink); }
  .card-contacts li { display: flex; align-items: center; gap: 6px; }
  .card-contacts svg { width: 12px; height: 12px; fill: var(--ink); }

  .back-brand { position: absolute; left: 0; top: 42px; width: 553px; display: flex; flex-direction: column; align-items: center; }
  .back-brand .brand-dot { width: 70px; height: 70px; border-width: 4px; border-color: var(--card-white); margin-bottom: 30px; }
  .back-brand .brand-name { font-size: 46px; color: var(--card-white); }
  .back-brand .brand-place { font-size: 24px; letter-spacing: 2px; color: var(--card-white); margin-top: 8px; }
  .tagline { position: absolute; left: 0; top: 247px; width: 553px; font-size: 14px; }
</style>
</head>
<body>
  <div class="stage"></div>

  <header class="brand-lockup">
    <span class="brand-dot"></span>
    <h1 class="brand-name">SOLVÉRA</h1>
    <p class="brand-place">SAN DIEGO</p>
  </header>

  <section class="card card--front">
    <div class="card-brand">
      <span class="brand-dot"></span>
      <span class="brand-name">SOLVERA</span>
      <span class="brand-place">SAN DIEGO</span>
    </div>
    <div class="card-band"><span class="card-band__solid"></span><span class="card-band__fade"></span></div>
    <p class="card-role">Editor-In-Chief</p>
    <address class="card-address">
      Solvera San Diego Magazine<br>
      847 Quillon Avenue #310 San Diego,<br>
      CA 92101
    </address>
    <ul class="card-contacts">
      <li><svg viewBox="0 0 12 12"><path d="M1 0h10v12H1z M3 2v8h6V2z"/></svg>000-000-0000</li>
      <li><svg viewBox="0 0 12 12"><path d="M3 0h6v4H3z M0 5h12v5H0z M3 8h6v4H3z"/></svg>000-000-0000</li>
      <li><svg viewBox="0 0 12 12"><path d="M0 5l6-5 6 5v7H0z M1.5 5.5l4.5 3.5 4.5-3.5"/></svg>ned@quorvix.com</li>
    </ul>
  </section>

  <section class="card card--back">
    <div class="back-brand">
      <span class="brand-dot"></span>
      <span class="brand-name">SOLVERA</span>
      <span class="brand-place">SAN DIEGO</span>
    </div>
    <p class="tagline">HEALTH, WELLNESS and YOGA LIFESTYLE</p>
  </section>
</body>
</html>
```